Book cover for book about Climate Change

Looking for a clean, bold, and attractive cover for a mass-market paperback (5.5"x 8.5") about solving the climate change problem. Title is either "Where the Rivers Meet” or A Harbor Made of Glass” (your choice), subtitle is "A practical field guide to mending the weather — so that the young ones after us inherit steady seasons and open skies," author is Lorne Whitcombe. Thinking that it *might* feature an image of Earth (or a portion thereof) and its very thin layer of atmosphere -- but STRONGLY encourage other ideas too!

Requirements
Nice to have
• Keep it positive — NOT scary doom-and-gloom

```html
<!DOCTYPE html>
<html lang="en">
<head>
<meta charset="utf-8">
<title>Where the Rivers Meet — Lorne Whitcombe</title>
<link rel="stylesheet" href="https://fonts.googleapis.com/css2?family=Oswald:wght@200;600&family=Montserrat:wght@700&family=Archivo:wght@700&display=swap">
<style>
  :root {
    --page: #ffffff;
    --sky-top: #0c0a0d;
    --sky-mid: #2a1628;
    --sky-low: #4a1e3c;
    --sky-glow: #6a2a4a;
    --ink: #fbfbfd;
    --accent: #f2b51f;
  }
  html, body {
    margin: 0;
    width: 1200px;
    height: 1200px;
    overflow: hidden;
    background: var(--page);
  }
  .cover {
    position: absolute;
    left: 259px;
    top: 64px;
    width: 704px;
    height: 1088px;
    overflow: hidden;
    color: var(--ink);
  }
  .cover-art {
    position: absolute;
    inset: 0;
    background:
      radial-gradient(ellipse 80% 45% at 60% 75%, var(--sky-glow) 0%, transparent 70%),
      linear-gradient(180deg, var(--sky-top) 0%, var(--sky-top) 22%, var(--sky-mid) 45%, var(--sky-low) 75%, var(--sky-mid) 100%);
  }
  .author {
    position: absolute;
    top: 62px;
    left: 0;
    right: 0;
    margin: 0;
    text-align: center;
    font-family: "Montserrat", sans-serif;
    font-weight: 700;
    font-size: 46px;
    letter-spacing: 0.2em;
    color: var(--accent);
    padding-left: 0.2em;
  }
  .title {
    position: absolute;
    top: 160px;
    left: 0;
    right: 0;
    margin: 0;
    display: flex;
    flex-direction: column;
    align-items: center;
    font-family: "Oswald", sans-serif;
    text-transform: uppercase;
    line-height: 0.98;
  }
  .title-strong {
    font-weight: 600;
    font-size: 200px;
    letter-spacing: -0.01em;
  }
  .title-light {
    font-weight: 200;
    font-size: 150px;
    margin: 4px 0;
  }
  .subtitle {
    position: absolute;
    left: 60px;
    right: 60px;
    top: 948px;
    margin: 0;
    text-align: center;
    font-family: "Archivo", sans-serif;
    font-weight: 700;
    font-size: 19px;
    line-height: 1.3;
    text-transform: uppercase;
    letter-spacing: 0.005em;
  }
  .subtitle em {
    font-style: normal;
    color: var(--accent);
  }
</style>
</head>
<body>
  <main class="cover">
    <div class="cover-art" role="img" aria-label="Night sky photograph full of stars, dark at the top fading into a purple and magenta glow of the Milky Way"></div>
    <p class="author">Lorne Whitcombe</p>
    <h1 class="title">
      <span class="title-strong">Where</span>
      <span class="title-light">the</span>
      <span class="title-strong">Rivers</span>
      <span class="title-light">Meet</span>
    </h1>
    <p class="subtitle">A <em>practical</em> field guide to <em>mending</em> the weather — so that the young ones after us inherit steady seasons and open skies,</p>
  </main>
</body>
</html>
```